RM Installations Web Site Design

Need a basic site to show clients a little about what we do. We are a custom audio video company in the high-end residential market. Need a few basic but professional pages to show past projects and products we sell. No e-commerce. Should include my new logo from MarkBazaar.

Industry/Entity Type

Residential

Number of Pages Required

2 page

Font styles to use
Serif
Sans Serif

Colors
f78f20

Requirements
Must have
• Company Logo, Send feedback page
Nice to have
• I have no ideas about design, but I do know what I like and dislike when I see it.

```html
<!DOCTYPE html>
<html lang="en">
<head>
<meta charset="utf-8">
<title>RM Installations — Custom Audio Video</title>
<link href="https://fonts.googleapis.com/css2?family=Lato:wght@300;400;700&display=swap" rel="stylesheet">
<style>
:root{
  --orange:#f78f20;
  --ink:#1b1b1b;
  --text:#333;
  --rule:#cfcfcf;
  --white:#fff;
  --footer:#262626;
}
*{box-sizing:border-box;margin:0;padding:0}
html,body{width:870px;height:1200px;overflow:hidden;background:var(--white)}
body{font-family:'Lato',sans-serif;color:var(--text);position:relative}
.abs{position:absolute}

.site-header{position:absolute;left:0;top:0;width:870px;height:88px}
.brand{position:absolute;left:94px;top:26px;display:flex;align-items:center;gap:10px}
.brand-mark{width:28px;height:28px;border-radius:50%;background:var(--orange)}
.brand-name{font-size:20px;font-weight:700;color:var(--ink);letter-spacing:.5px}
.callout{position:absolute;left:652px;top:10px;display:flex;align-items:center;gap:8px}
.callout-label{font-size:10px;letter-spacing:1.5px;color:var(--ink);font-weight:700}
.callout-number{font-size:15px;color:var(--ink);font-weight:700;margin-top:1px}
.main-nav{position:absolute;left:320px;top:60px;display:flex;align-items:center;height:16px}
.main-nav a{font-size:10px;font-weight:700;color:var(--ink);text-decoration:none;padding:0 11px;border-left:1px solid #bbb;line-height:14px}
.main-nav a.home{border-left:none;padding:0 11px 0 2px}

.hero{position:absolute;left:0;top:88px;width:870px;height:354px;
  background:radial-gradient(ellipse at 75% 25%,#6a4aa0 0%,transparent 35%),
  linear-gradient(100deg,#3a2420 0%,#9a5a3a 30%,#6b4030 55%,#2a1812 100%)}
.hero-caption{position:absolute;left:0;bottom:0;width:100%;height:42px;background:rgba(30,22,20,.65);
  color:var(--white);font-size:20px;font-weight:400;text-align:center;line-height:42px}
.hero-arrow{position:absolute;top:158px}

.section-title{position:absolute;left:0;width:870px;text-align:center;font-size:21px;font-weight:400;color:var(--ink);letter-spacing:.3px}
.divider{position:absolute;left:170px;width:530px;height:10px}
.divider::before,.divider::after{content:"";position:absolute;top:4px;width:246px;height:1px;background:var(--rule)}
.divider::before{left:0}.divider::after{right:0}
.divider .dot{position:absolute;left:260px;top:0;width:10px;height:10px;border-radius:50%;background:var(--orange)}
.divider.dark::before,.divider.dark::after{background:var(--ink)}
.divider.dark .dot{background:var(--ink)}

.intro{position:absolute;left:96px;top:525px;width:678px;text-align:center;font-size:11px;line-height:17.6px;color:var(--text)}
.btn{position:absolute;left:380px;top:594px;width:110px;height:26px;background:var(--ink);color:var(--white);
  border-radius:4px;font-size:11px;font-weight:700;text-align:center;line-height:26px}

.services{position:absolute;left:0;top:658px;width:870px;height:267px;background:var(--orange)}
.service{position:absolute;top:101px;width:160px;text-align:center}
.service-icon{display:block;margin:0 auto}
.service-label{margin-top:17px;font-size:14px;line-height:18px;color:var(--ink);text-transform:uppercase}
.service-sep{position:absolute;top:100px;width:1px;height:134px;background:rgba(0,0,0,.12)}

.thumb{position:absolute;top:1017px;width:156px;height:111px}
.thumb-caption{position:absolute;inset:0;display:flex;align-items:center;justify-content:center;text-align:center;
  color:var(--white);font-size:14px;line-height:18px;font-weight:300}

.site-footer{position:absolute;left:0;top:1163px;width:870px;height:37px;background:var(--footer);
  color:#ddd;font-size:10.5px;text-align:center;line-height:37px}
</style>
</head>
<body>

<header class="site-header">
  <div class="brand"><span class="brand-mark"></span><span class="brand-name">RM INSTALLATIONS</span></div>
  <div class="callout">
    <svg width="28" height="28" viewBox="0 0 28 28"><circle cx="14" cy="14" r="12.5" fill="none" stroke="var(--orange)" stroke-width="1.5"/>
      <path d="M10 8c-1 1-1.5 2-1 4 1 3 4 6.5 7 7.5 2 .5 3 0 4-1l-2.3-2.3-1.6 1c-1.6-.7-3.6-2.7-4.3-4.3l1-1.6z" fill="var(--orange)"/></svg>
    <div><div class="callout-label">CALL US TODAY</div><div class="callout-number">555 013 2480</div></div>
  </div>
  <nav class="main-nav">
    <a class="home" href="#" aria-label="Home"><svg width="13" height="12" viewBox="0 0 13 12"><path d="M6.5 0 13 6h-2v6H8V8H5v4H2V6H0z" fill="var(--orange)"/></svg></a>
    <a href="#">ABOUT US</a><a href="#">PRODUCT &amp; SERVICES</a><a href="#">PAST PROJECTS</a><a href="#">FEEDBACK</a><a href="#">CONTACT US</a>
  </nav>
</header>

<section class="hero" role="img" aria-label="Dim living room with a lounge chair facing a wall-mounted television under warm and violet lighting">
  <svg class="hero-arrow" style="left:41px" width="34" height="34" viewBox="0 0 34 34"><circle cx="17" cy="17" r="15.5" fill="rgba(0,0,0,.25)" stroke="#ccc" stroke-width="1.5"/><path d="M19 10l-7 7 7 7" fill="none" stroke="#fff" stroke-width="1.5"/></svg>
  <svg class="hero-arrow" style="left:795px" width="34" height="34" viewBox="0 0 34 34"><circle cx="17" cy="17" r="15.5" fill="rgba(0,0,0,.25)" stroke="#ccc" stroke-width="1.5"/><path d="M15 10l7 7-7 7" fill="none" stroke="#fff" stroke-width="1.5"/></svg>
  <div class="hero-caption">We are a custom audio video company in the high-end residential market</div>
</section>

<h1 class="section-title" style="top:470px">WELCOME TO RM INSTALLATIONS</h1>
<div class="divider" style="top:504px"><span class="dot"></span></div>
<p class="intro">Lorem ipsum dolor sit amet, consectetuer adipiscing elit, sed diam nonummy nibh euismod tincidunt ut laoreet dolore magna aliquam erat volutpat. Ut wisi enim ad minim veniam, quis nostrud exerci tation ullamcorper suscipit lobortis nisl ut aliquip ex ea commodo consequat. Duis autem vel eum iriure dolor in hendrerit in vulputate velit esse molestie consequat, vel illum dolore eu feugiat nulla facilisis at vero.</p>
<div class="btn">READ MORE</div>

<section class="services">
  <h2 class="section-title" style="top:31px">PRODUCT &amp; SERVICES</h2>
  <div class="divider dark" style="top:65px"><span class="dot"></span></div>
  <svg class="abs" style="left:58px;top:144px" width="24" height="46" viewBox="0 0 24 46"><path d="M23 1 1 23l22 22" fill="none" stroke="var(--ink)" stroke-width="1.2"/></svg>
  <svg class="abs" style="left:788px;top:144px" width="24" height="46" viewBox="0 0 24 46"><path d="M1 1l22 22L1 45" fill="none" stroke="var(--ink)" stroke-width="1.2"/></svg>

  <div class="service" style="left:112px">
    <svg class="service-icon" width="86" height="86" viewBox="0 0 86 86"><circle cx="43" cy="43" r="41" fill="none" stroke="var(--ink)" stroke-width="2.5"/>
      <rect x="26" y="34" width="34" height="24" rx="3" fill="none" stroke="var(--ink)" stroke-width="4"/><path d="M36 33l-5-6M40 33l5-6" stroke="var(--ink)" stroke-width="2"/><rect x="50" y="40" width="5" height="6" fill="var(--ink)"/></svg>
    <div class="service-label">Distributed<br>Video</div>
  </div>
  <div class="service-sep" style="left:273px"></div>
  <div class="service" style="left:273px">
    <svg class="service-icon" width="86" height="86" viewBox="0 0 86 86"><circle cx="43" cy="43" r="41" fill="none" stroke="var(--ink)" stroke-width="2.5"/>
      <circle cx="43" cy="43" r="21" fill="none" stroke="var(--ink)" stroke-width="4"/><path d="M37 33v20l16-10z" fill="var(--ink)"/></svg>
    <div class="service-label">Media<br>Rooms</div>
  </div>
  <div class="service-sep" style="left:434px"></div>
  <div class="service" style="left:435px">
    <svg class="service-icon" width="86" height="86" viewBox="0 0 86 86"><circle cx="43" cy="43" r="41" fill="none" stroke="var(--ink)" stroke-width="2.5"/>
      <path d="M24 44 43 26l19 18" fill="none" stroke="var(--ink)" stroke-width="5"/><path d="M30 44v16h9V50h8v10h9V44L43 32z" fill="var(--ink)"/></svg>
    <div class="service-label">Residential<br>Cinemas</div>
  </div>
  <div class="service-sep" style="left:596px"></div>
  <div class="service" style="left:597px">
    <svg class="service-icon" width="86" height="86" viewBox="0 0 86 86"><circle cx="43" cy="43" r="41" fill="none" stroke="var(--ink)" stroke-width="2.5"/>
      <rect x="32" y="22" width="12" height="30" rx="3" transform="rotate(-25 38 37)" fill="var(--ink)"/><path d="M38 46l8-4 10 14-8 6z" fill="var(--ink)"/></svg>
    <div class="service-label">Whole-House<br>Control Systems</div>
  </div>
</section>

<h2 class="section-title" style="top:954px">PAST PROJECTS</h2>
<div class="divider" style="top:988px"><span class="dot"></span></div>
<svg class="abs" style="left:58px;top:1050px" width="24" height="46" viewBox="0 0 24 46"><path d="M23 1 1 23l22 22" fill="none" stroke="var(--ink)" stroke-width="1.2"/></svg>
<svg class="abs" style="left:788px;top:1050px" width="24" height="46" viewBox="0 0 24 46"><path d="M1 1l22 22L1 45" fill="none" stroke="var(--ink)" stroke-width="1.2"/></svg>

<div class="thumb" style="left:94px;background:radial-gradient(circle at 50% 40%,#6a1a1a,#3a0808)" role="img" aria-label="Red-walled private home cinema with screen and seating">
  <div class="thumb-caption">Lorem ipsum dolor<br>sit amet</div>
</div>
<div class="thumb" style="left:269px;background:linear-gradient(90deg,#6e6040,#a09670 50%,#6a5c3c)" role="img" aria-label="Hand holding a remote beside wall-mounted light switches and keypad"></div>
<div class="thumb" style="left:444px;background:radial-gradient(circle at 40% 50%,#555,#111 70%)" role="img" aria-label="Speakers and audio amplifier equipment"></div>
<div class="thumb" style="left:619px;background:linear-gradient(180deg,#c8d4dc 0%,#7a8a70 60%,#5a7a50 100%)" role="img" aria-label="Outdoor television under a patio showing a baseball game"></div>

<footer class="site-footer">Copyright © 2015 RM INSTALLATIONS. All Rights Reserved</footer>

</body>
</html>
```